We are a local Communty Pharmacy wishing to promote and market a specialised Pharmaceutical Service

We would like a design that is professional and enticing ( according to the brief In attached files)
We wish to Market Compounding Pharmacy as a specialist side of our business.
We have the expertise a purpose built preparation laboratory.
The main purpose is an Internet presence that entices prospective patients to contact or visit our physical store.

Target Market(s)

Patients Medicos and Veterinary clients

Industry/Entity Type

Pharmacy

Coding

Coded - Design and coding required

Number of Pages Required

1 page

Requirements
Must have
• Clear friendly image
Nice to have
• soft enticing feel
Should not have
• No crass loud unprofessional elements

```html
<!DOCTYPE html>
<html lang="en">
<head>
<meta charset="utf-8">
<title>Bellmere Compounding Pharmacy</title>
<link href="https://fonts.googleapis.com/css2?family=Open+Sans:wght@400;600;700&family=Oswald:wght@400;500&display=swap" rel="stylesheet">
<style>
  :root {
    --blue: #1e88d0;
    --blue-dark: #15679f;
    --orange: #f0931e;
    --ink: #3a3f44;
    --muted: #6b7278;
    --line: #dfe3e6;
    --footer: #2b2f33;
    --footer-deep: #1f2225;
    --bg: #ffffff;
  }
  * { box-sizing: border-box; margin: 0; padding: 0; }
  html, body { width: 744px; height: 1200px; overflow: hidden; background: var(--bg); }
  body { font-family: "Open Sans", Arial, sans-serif; color: var(--ink); position: relative; }

  .site-header { height: 82px; display: flex; align-items: center; justify-content: space-between; padding: 0 28px; position: relative; }
  .brand { display: flex; align-items: center; gap: 8px; }
  .brand-mark { width: 30px; height: 30px; background: var(--blue); border-radius: 50%; }
  .brand-name { font-size: 17px; font-weight: 700; color: var(--blue-dark); line-height: 1.1; }
  .brand-name small { display: block; font-size: 10px; font-weight: 700; color: var(--blue-dark); letter-spacing: .3px; }
  .top-phones { position: absolute; top: 6px; right: 28px; display: flex; gap: 16px; font-size: 8px; color: var(--muted); }
  .top-phones span::before { content: ""; display: inline-block; width: 6px; height: 6px; background: var(--blue); border-radius: 50%; margin-right: 4px; vertical-align: middle; }
  .main-nav { display: flex; margin-top: 14px; }
  .main-nav a { font-size: 9.5px; color: var(--ink); text-decoration: none; padding: 6px 9px; }
  .main-nav a.active { background: var(--blue); color: #fff; }

  .hero { position: relative; height: 350px; background: linear-gradient(90deg, #b8c6cc 0%, #d9e2e5 40%, #eef2f3 70%, #e2e9eb 100%); }
  .hero-photo { position: absolute; inset: 0; }
  .hero-person { position: absolute; right: 80px; top: 0; width: 200px; height: 350px; background: linear-gradient(180deg, #efe4da 0%, #ffffff 40%, #f4f6f7 100%); border-radius: 90px 90px 0 0; opacity: .85; }
  .hero-title { position: absolute; left: 0; top: 96px; background: rgba(30,136,208,.85); color: #fff; font-family: "Oswald", sans-serif; font-size: 22px; letter-spacing: 1px; padding: 8px 20px 8px 54px; }
  .hero-sub { position: absolute; left: 0; top: 142px; background: rgba(240,147,30,.9); color: #fff; font-size: 10px; font-weight: 600; padding: 6px 16px 6px 54px; }
  .hero-arrows { position: absolute; left: 54px; top: 224px; display: flex; gap: 8px; }
  .hero-arrows span { width: 26px; height: 26px; background: #3b4147; display: flex; align-items: center; justify-content: center; }

  .section-title { display: flex; align-items: center; justify-content: center; gap: 12px; font-size: 17px; font-weight: 700; color: var(--blue-dark); }
  .section-title::before, .section-title::after { content: ""; width: 110px; height: 1px; background: var(--line); }
  .section-title i { width: 12px; height: 12px; border-radius: 50%; border: 3px solid var(--blue); }
  .about { padding: 28px 40px 0; }
  .about p { font-size: 7.5px; line-height: 1.65; color: var(--muted); margin-top: 10px; text-align: justify; }

  .features { padding: 30px 40px 0; }
  .feature-grid { display: flex; justify-content: space-between; margin-top: 20px; }
  .feature-card { width: 206px; }
  .feature-img { height: 200px; border: 1px solid var(--line); }
  .feature-card:nth-child(1) .feature-img { background: linear-gradient(160deg, #eef0f2, #4a3d55); }
  .feature-card:nth-child(2) .feature-img { background: linear-gradient(160deg, #fafafa, #d8e4ef); }
  .feature-card:nth-child(3) .feature-img { background: linear-gradient(160deg, #fdfdfd, #e8b4b0); }
  .feature-label { font-size: 9px; font-weight: 600; text-align: center; padding: 10px 0; border: 1px solid var(--line); border-top: 3px solid var(--blue); }

  .site-footer { position: absolute; top: 982px; left: 0; width: 744px; height: 184px; background: var(--footer); display: flex; }
  .hours { width: 150px; margin-left: 28px; background: var(--blue); color: #fff; text-align: center; padding-top: 18px; }
  .hours h3 { font-family: "Oswald", sans-serif; font-weight: 400; font-size: 15px; margin-top: 6px; }
  .hours .days { font-family: "Oswald", sans-serif; font-size: 18px; margin-top: 4px; }
  .hours .time { display: inline-block; background: #fff; color: var(--blue-dark); font-size: 9px; font-weight: 700; padding: 5px 10px; margin-top: 14px; }
  .map { flex: 1; margin: 0 20px; background: linear-gradient(135deg, #e9e6df, #d8e0d3); }
  .contact { width: 190px; color: #cfd3d6; padding-top: 22px; padding-right: 28px; font-size: 8px; }
  .contact h4 { font-family: "Oswald", sans-serif; font-weight: 400; font-size: 14px; color: #fff; margin-bottom: 12px; }
  .contact li { list-style: none; margin-bottom: 8px; display: flex; align-items: center; gap: 6px; }
  .contact li::before { content: ""; width: 10px; height: 10px; border-radius: 50%; background: var(--blue); flex: none; }
  .bottom-bar { position: absolute; top: 1166px; left: 0; width: 744px; height: 34px; background: var(--footer-deep); display: flex; align-items: center; justify-content: space-between; padding: 0 28px; font-size: 8px; color: #9aa0a5; }
  .social { display: flex; gap: 8px; }
  .social span { width: 14px; height: 14px; border-radius: 50%; background: #4a5056; }
</style>
</head>
<body>
  <header class="site-header">
    <div class="brand">
      <span class="brand-mark"></span>
      <span class="brand-name">BELLMERE<small>Compounding Pharmacy</small></span>
    </div>
    <div class="top-phones"><span>08 5550 1420</span><span>08 5550 1421</span></div>
    <nav class="main-nav">
      <a href="#">Home</a><a href="#" class="active">About Us</a><a href="#">Pages</a><a href="#">Promotions</a><a href="#">Gallery</a><a href="#">Contact Us</a>
    </nav>
  </header>

  <section class="hero">
    <div class="hero-photo" role="img" aria-label="Smiling pharmacist in a white coat holding a medicine bottle in a bright pharmacy"><div class="hero-person"></div></div>
    <h1 class="hero-title">COMPOUNDING PHARMACY</h1>
    <p class="hero-sub">CUSTOMISED MEDICATIONS FOR PATIENTS</p>
    <div class="hero-arrows">
      <span><svg width="10" height="10" viewBox="0 0 10 10"><path d="M7 1 3 5l4 4" stroke="#fff" stroke-width="2" fill="none"/></svg></span>
      <span><svg width="10" height="10" viewBox="0 0 10 10"><path d="M3 1l4 4-4 4" stroke="#fff" stroke-width="2" fill="none"/></svg></span>
    </div>
  </section>

  <section class="about">
    <h2 class="section-title"><i></i>WHAT IS COMPOUNDING PHARMACY?<i></i></h2>
    <p>Compounding is the art of preparing medicines to suit the exact needs of each patient. Long before mass production, every pharmacist mixed remedies by hand, and today that skill returns in a modern form. In our purpose built laboratory we prepare creams, capsules, lozenges and liquids in strengths and flavours that are not available from the shelf. This helps people with allergies to common fillers, children who refuse bitter tastes, and older patients who find tablets hard to swallow.</p>
    <p>Our trained team works closely with doctors, dentists and veterinarians to design each preparation. Every formula is checked, recorded and made to strict quality standards, using pure ingredients from trusted suppliers. Whether you need a hormone cream, a pain gel or a chewable treat for a pet, we are happy to talk through your options. Visit our store or call us to learn how a tailored medicine could make your treatment simpler and more comfortable.</p>
  </section>

  <section class="features">
    <h2 class="section-title"><i></i>FEATURE ITEMS<i></i></h2>
    <div class="feature-grid">
      <article class="feature-card"><div class="feature-img" role="img" aria-label="Vitamin syrup product box and bottle"></div><div class="feature-label">VIT ARTICLE</div></article>
      <article class="feature-card"><div class="feature-img" role="img" aria-label="Soap therapy product pack"></div><div class="feature-label">SOAP THERAPHY</div></article>
      <article class="feature-card"><div class="feature-img" role="img" aria-label="Thyroid extract product box"></div><div class="feature-label">THYROID EXTRACT</div></article>
    </div>
  </section>

  <footer class="site-footer">
    <div class="hours">
      <svg width="26" height="26" viewBox="0 0 26 26"><circle cx="13" cy="13" r="11" stroke="#fff" stroke-width="2" fill="none"/><path d="M13 6v7l5 3" stroke="#fff" stroke-width="2" fill="none"/></svg>
      <h3>HOURS</h3>
      <div class="days">7 DAYS A WEEK</div>
      <div class="time">8.30 A.M TO 8.30 P.M</div>
    </div>
    <div class="map" role="img" aria-label="Street map showing the pharmacy location"></div>
    <div class="contact">
      <h4>CONTACTS</h4>
      <ul>
        <li>08 5550 1420</li>
        <li>08 5550 1421</li>
        <li>12 Harbour Road, Bellmere</li>
        <li>info@bellmerepharmacy.example</li>
        <li>care@bellmerepharmacy.example</li>
      </ul>
    </div>
  </footer>
  <div class="bottom-bar">
    <span>© Copyright Compounding Pharmacy. All Rights Reserved.</span>
    <div class="social"><span></span><span></span><span></span><span></span></div>
  </div>
</body>
</html>
```